GJ & DW Fencing Pty Ltd

We already have an existing logo created by Pixel Harbour however we have restructured to a company. We would like someone to add Pty Ltd to our business name please.

Colors

Designer to choose only greyscale colors for use in the design.

```html
<!DOCTYPE html>
<html lang="en">
<head>
<meta charset="utf-8">
<title>GJ &amp; DW Fencing Pty Ltd – Business Card</title>
<link href="https://fonts.googleapis.com/css2?family=Old+Standard+TT:wght@400;700&family=Raleway:wght@300;400&display=swap" rel="stylesheet">
<style>
  :root {
    --page-bg: #d9d9d9;
    --card-dark: #0c0c0c;
    --card-mid: #2e2e2e;
    --card-sheen: #4a4a4a;
    --ink-light: #f2f2f2;
    --ink-soft: #cfcfcf;
    --rule: #9a9a9a;
    --stripe: #f5f5f5;
    --stripe-shade: #8c8c8c;
  }
  * { margin: 0; padding: 0; box-sizing: border-box; }
  html, body {
    width: 1200px; height: 1022px; overflow: hidden;
    background: var(--page-bg);
  }
  .stage {
    width: 1200px; height: 1022px;
    display: flex; align-items: center; justify-content: center;
  }
  .business-card {
    position: relative;
    width: 1000px; height: 572px;
    border-radius: 14px;
    overflow: hidden;
    background: radial-gradient(ellipse at 45% 40%, var(--card-sheen) 0%, var(--card-mid) 35%, var(--card-dark) 80%);
    box-shadow: 0 18px 40px rgba(0,0,0,0.35);
    color: var(--ink-light);
  }
  .brand {
    position: absolute; left: 80px; top: 110px;
    display: flex; align-items: center; gap: 22px;
  }
  .brand-mark {
    width: 60px; height: 60px; border-radius: 50%;
    background: var(--ink-light);
  }
  .brand-name {
    font-family: "Old Standard TT", serif;
    font-weight: 700;
    font-size: 50px;
    line-height: 1;
    color: var(--ink-light);
    letter-spacing: 1px;
  }
  .divider {
    position: absolute; left: 80px; right: 80px; top: 262px;
    height: 1px; background: var(--rule);
  }
  .holder {
    position: absolute; left: 80px; top: 318px;
    font-family: "Old Standard TT", serif;
    font-size: 34px; letter-spacing: 4px;
    color: var(--ink-soft);
    text-transform: uppercase;
  }
  .holder-rule {
    position: absolute; left: 80px; top: 378px;
    width: 330px; height: 1px; background: var(--rule);
  }
  .contact-list {
    position: absolute; right: 80px; top: 300px;
    list-style: none;
    font-family: "Raleway", sans-serif;
    font-weight: 300; font-size: 24px;
    color: var(--ink-light);
  }
  .contact-list li {
    display: flex; align-items: center; justify-content: flex-end;
    gap: 16px; height: 42px;
  }
  .contact-icon {
    width: 26px; height: 26px; border-radius: 50%;
    background: var(--ink-light);
    display: flex; align-items: center; justify-content: center;
  }
  .contact-icon svg { width: 15px; height: 15px; }
  .edge-stripes {
    position: absolute; left: 0; bottom: 0; width: 1000px; height: 70px;
  }
</style>
</head>
<body>
<main class="stage">
  <section class="business-card">
    <div class="brand">
      <span class="brand-mark"></span>
      <span class="brand-name">GJ &amp; DW Fencing Pty Ltd</span>
    </div>

    <div class="divider"></div>

    <p class="holder">Sam Carrow</p>
    <div class="holder-rule"></div>

    <ul class="contact-list">
      <li>PO Box 418 Karrinup WA 6512
        <span class="contact-icon">
          <svg viewBox="0 0 16 16"><path d="M2 8 L8 2.5 L14 8 M4 7 V14 H12 V7" fill="none" stroke="#111" stroke-width="2"/></svg>
        </span>
      </li>
      <li>0412 555 019
        <span class="contact-icon">
          <svg viewBox="0 0 16 16"><path d="M4 2 L6.5 5 L5 6.8 C6 9 7 10 9.2 11 L11 9.5 L14 12 L12.5 14 C7 13.5 2.5 9 2 3.5 Z" fill="#111"/></svg>
        </span>
      </li>
      <li>office@gjdwfencing.au
        <span class="contact-icon">
          <svg viewBox="0 0 16 16"><rect x="2" y="4" width="12" height="8.5" fill="none" stroke="#111" stroke-width="1.6"/><path d="M2 4 L8 9 L14 4" fill="none" stroke="#111" stroke-width="1.6"/></svg>
        </span>
      </li>
    </ul>

    <svg class="edge-stripes" viewBox="0 0 1000 70" preserveAspectRatio="none">
      <path d="M0 20 H640 L680 0 H1000 V8 H684 L644 28 H0 Z" fill="var(--stripe)"/>
      <path d="M0 34 H648 L688 14 H1000 V22 H692 L652 42 H0 Z" fill="var(--stripe-shade)"/>
      <path d="M0 48 H656 L696 28 H1000 V36 H700 L660 56 H0 Z" fill="var(--stripe)"/>
      <path d="M0 62 H664 L704 42 H1000 V50 H708 L668 70 H0 Z" fill="var(--stripe-shade)"/>
    </svg>
  </section>
</main>
</body>
</html>
```